Visitenkarten-Design für Sonnen-/Fensterschutz
Zielgruppe
KLW GmbH ist eine Firma, die Sonnenschutz und Fensterschutz anbieten.
'Ihr kompetenter Partner in Sachen Sonnenschutz- , Fenster- und Türtechnik. Sie erhalten echtes Handwerk aus dem Mühlviertel zu fairen Preisen.'
Unsere Zielgruppe sind Personen mit Haus, die am Land leben.
Firmenname: KLW GmbH
Slogan: Fenster & Sonnenschutz
Aufgabenstellung
Hier befindet sich das Logodesign: https://dx.qv/t-QwLpo7RbNs
Bitte ein schlichtes Design bereitstellen mit einer Dummy-Person:
Jonas Weidlinger + Telefonnummer + Email
Die finalen Daten bitte erst am Schluss berücksichtigen (für Gewinnerdesign)
Gerne auch hintern + vorne bedruckbar bereitstellen.

```html
<!DOCTYPE html>
<html lang="de">
<head>
<meta charset="utf-8">
<title>KLW GmbH – Visitenkarte</title>
<link href="https://fonts.googleapis.com/css2?family=Open+Sans:wght@400;600;700&display=swap" rel="stylesheet">
<style>
  :root {
    --bg: #1d1d1d;
    --card: #363636;
    --orange: #e0782a;
    --red: #c8352a;
    --text: #e9e9e9;
    --muted: #bdbdbd;
  }
  * { box-sizing: border-box; margin: 0; padding: 0; }
  html, body { width: 1200px; height: 801px; overflow: hidden; }
  body {
    background: var(--bg);
    font-family: "Open Sans", Arial, sans-serif;
    position: relative;
  }
  .card {
    position: absolute;
    top: 232px;
    width: 520px;
    height: 336px;
    background: var(--card);
    border-radius: 4px;
    overflow: hidden;
    box-shadow: 0 14px 40px rgba(0,0,0,.55);
  }
  .card--front { left: 45px; }
  .card--back { left: 635px; }

  .brand {
    position: absolute;
    left: 34px;
    top: 34px;
    display: flex;
    align-items: center;
    gap: 12px;
  }
  .brand__square {
    width: 30px; height: 30px;
    background: var(--orange);
  }
  .brand__name {
    font-weight: 700;
    font-size: 36px;
    line-height: 1;
    color: var(--orange);
    letter-spacing: 1px;
    white-space: nowrap;
  }
  .slogan {
    position: absolute;
    left: 34px;
    top: 80px;
    font-size: 12px;
    font-weight: 600;
    letter-spacing: 1.5px;
    color: var(--red);
    text-transform: uppercase;
  }
  .contact {
    position: absolute;
    left: 290px;
    top: 112px;
    width: 200px;
    font-size: 11.5px;
    line-height: 1.55;
    color: var(--muted);
  }
  .contact__company {
    font-weight: 700;
    font-size: 14px;
    color: var(--text);
    margin-bottom: 4px;
  }
  .contact__row {
    display: flex;
    align-items: flex-start;
    gap: 8px;
    margin-top: 6px;
  }
  .contact__row svg { flex: none; margin-top: 3px; }
  .person {
    position: absolute;
    left: 34px;
    bottom: 52px;
    color: var(--text);
  }
  .person__name { font-size: 22px; font-weight: 600; }
  .person__role { font-size: 14px; color: var(--muted); margin-top: 2px; }
  .stripes {
    position: absolute;
    inset: 0;
  }
  .back__brand {
    position: absolute;
    inset: 0;
    display: flex;
    flex-direction: column;
    align-items: center;
    justify-content: center;
    gap: 10px;
  }
  .back__name {
    font-weight: 700;
    font-size: 64px;
    line-height: 1;
    color: var(--orange);
    letter-spacing: 2px;
  }
  .back__slogan {
    font-size: 14px;
    font-weight: 600;
    letter-spacing: 2px;
    color: var(--red);
    text-transform: uppercase;
  }
</style>
</head>
<body>
  <section class="card card--front" aria-label="Vorderseite">
    <svg class="stripes" width="520" height="336" viewBox="0 0 520 336" aria-hidden="true">
      <defs>
        <linearGradient id="band" x1="0" y1="1" x2="1" y2="0">
          <stop offset="0" stop-color="#c8352a"/>
          <stop offset="1" stop-color="#e0782a"/>
        </linearGradient>
      </defs>
      <polygon points="320,336 520,206 520,220 340,336" fill="url(#band)"/>
      <polygon points="352,336 520,228 520,246 378,336" fill="url(#band)"/>
      <polygon points="392,336 520,256 520,266 406,336" fill="url(#band)"/>
    </svg>

    <div class="brand">
      <span class="brand__square"></span>
      <span class="brand__name">KLW GmbH</span>
    </div>
    <p class="slogan">Fenster &amp; Sonnenschutz</p>

    <div class="contact">
      <p class="contact__company">KLW GmbH</p>
      <div class="contact__row">
        <svg width="12" height="12" viewBox="0 0 12 12" aria-hidden="true"><path d="M6 0C3.8 0 2 1.8 2 4c0 3 4 8 4 8s4-5 4-8c0-2.2-1.8-4-4-4zm0 5.5A1.5 1.5 0 1 1 6 2.5a1.5 1.5 0 0 1 0 3z" fill="var(--red)"/></svg>
        <span>Am Kirchfeld 21-23<br>4240 Freistadt</span>
      </div>
      <div class="contact__row">
        <svg width="12" height="12" viewBox="0 0 12 12" aria-hidden="true"><path d="M2.5 0.5l2 2.5-1.2 1.3c.7 1.6 2 2.9 3.5 3.6L8 6.6l2.5 2-1 2.4C4.7 11 1 7.3 1 2.5z" fill="var(--red)"/></svg>
        <span>+49 160 482 3071</span>
      </div>
      <div class="contact__row">
        <svg width="12" height="12" viewBox="0 0 12 12" aria-hidden="true"><rect x="0.5" y="2" width="11" height="8" fill="none" stroke="var(--red)" stroke-width="1.2"/><path d="M0.5 2.5L6 6.5l5.5-4" fill="none" stroke="var(--red)" stroke-width="1.2"/></svg>
        <span>info@klw-fenster.de</span>
      </div>
    </div>

    <div class="person">
      <p class="person__name">Jonas Weidlinger</p>
      <p class="person__role">Geschäftsführer</p>
    </div>
  </section>

  <section class="card card--back" aria-label="Rückseite">
    <div class="back__brand">
      <span class="back__name">KLW GmbH</span>
      <span class="back__slogan">Fenster &amp; Sonnenschutz</span>
    </div>
  </section>
</body>
</html>
```